Parcelwise HQ letterhead and envelope

Design a formal (8.5x11) letterhead and envelope for sales outreach and legal matters. Using design input from https://www.parcelwisehq.example/ and the attached documents.

Industry/Entity Type

Software Service

Requirements
Must have
• These 4 hex colors are our official colors:
• #355c98 [blue]
• #1eb1a2 [teal]
• #fdba12 [gold]
• #f1653b [orange]
• So no other colors besides these should be used.

```html
<!DOCTYPE html>
<html lang="en">
<head>
<meta charset="utf-8">
<title>Parcelwise HQ Letterhead</title>
<link rel="stylesheet" href="https://fonts.googleapis.com/css2?family=Lato:wght@400;700&family=Arimo&family=Damion&display=swap">
<style>
  :root {
    --brand-blue: #355c98;
    --brand-teal: #1eb1a2;
    --paper: #ffffff;
    --backdrop: #e4e4e4;
    --body-text: #555555;
    --ink: #222222;
  }
  html, body {
    margin: 0;
    width: 996px;
    height: 1200px;
    overflow: hidden;
    background: var(--backdrop);
  }
  .letterhead {
    position: absolute;
    left: 48px;
    top: 17px;
    width: 900px;
    height: 1165px;
    background: var(--paper);
    font-family: "Lato", sans-serif;
    overflow: hidden;
  }
  .edge-band-blue {
    position: absolute; left: 0; top: 0; width: 25px; height: 100%;
    background: var(--brand-blue);
  }
  .edge-band-teal {
    position: absolute; left: 25px; top: 0; width: 19px; height: 100%;
    background: var(--brand-teal);
  }
  .brand-name {
    position: absolute; right: 77px; top: 36px;
    color: var(--brand-blue);
    font-size: 34px; font-weight: 400; line-height: 40px;
  }
  .salutation {
    position: absolute; left: 77px; top: 257px;
    color: var(--brand-blue); font-weight: 700; font-size: 16px;
  }
  .letter-body {
    position: absolute; left: 77px; top: 285px; width: 747px;
    color: var(--body-text); font-size: 16.6px; line-height: 26.3px;
    text-align: justify;
  }
  .letter-body p { margin: 0 0 20px; }
  .closing {
    position: absolute; left: 77px; top: 753px;
    color: var(--ink); font-size: 19px;
  }
  .signature {
    position: absolute; left: 77px; top: 790px;
    color: var(--brand-blue); font-family: "Damion", cursive; font-size: 36px;
  }
  .contact-tab {
    position: absolute; left: 25px; top: 985px; width: 32px; height: 130px;
    background: var(--brand-blue); border-radius: 0 12px 12px 0;
  }
  .contact-icon { position: absolute; left: 31px; width: 20px; height: 20px; }
  .contact-list {
    position: absolute; left: 68px; top: 993px;
    font-family: "Arimo", sans-serif; font-size: 12.3px; line-height: 16.4px;
    color: var(--ink); letter-spacing: 0.3px; font-style: normal;
  }
  .contact-list div { margin-bottom: 8px; }
</style>
</head>
<body>
<main class="letterhead">
  <div class="edge-band-blue"></div>
  <div class="edge-band-teal"></div>

  <header class="brand-name">Parcelwise HQ</header>

  <div class="salutation">Dear Mr. Lorem,</div>

  <section class="letter-body">
    <p>Lorem ipsum dolor sit amet, consectetuer adipiscing elit, sed diam nonummy nibh euismod tinci&shy;dunt ut laoreet dolore magna aliquam erat volutpat. Ut wisi enim ad minim veniam, quis nostrud exerci tation ullamcorper suscipit lobortis nisl ut aliquip ex ea commodo consequat. Duis autem vel eum iriure dolor in hendiusto odio dignissim qui blandit praesent luptatum zzril delenit augue duis dolore te feugait nulla facilisi.</p>
    <p>Lorem ipsum dolor sit amet, consectetuer adipiscing elit, sed diam nonummy nibh euismod tinci&shy;dunt ut laoreet dolore magna aliquam erat volutpat. Ut wisi enim ad minim veniam, quis nostrud exerci tation ullamcorper suscipit lobortis nisl ut aliquip ex ea commodo consequat. Duis autem vel eum iriure dolor in hendiusto odio dignissim qui blandit praesent luptatum zzril delenit augue duis dolore te feugait nulla facilisi.</p>
    <p>Lorem ipsum dolor sit amet, consectetuer adipiscing elit, sed diam nonummy nibh euismod tinci&shy;dunt ut laoreet dolore magna aliquam erat volutpat. Ut wisi enim ad minim veniam, quis nostrud exerci tation ullamcorper suscipit lobortis nisl ut aliquip ex ea commodo consequat. Duis autem vel eum iriure dolor in hendiusto odio dignissim qui blandit praesent luptatum zzril delenit augue duis dolore te feugait nulla facilisi.</p>
  </section>

  <div class="closing">Sincerely Your,</div>
  <div class="signature">Your Name</div>

  <div class="contact-tab"></div>
  <svg class="contact-icon" style="top:998px" viewBox="0 0 20 20" aria-hidden="true">
    <circle cx="10" cy="10" r="8.5" fill="none" stroke="#fff" stroke-width="1.5"/>
    <path d="M7 5.5l1.6 2.2-1 1.2c.6 1.3 1.5 2.2 2.8 2.8l1.2-1 2.2 1.6-.8 1.8c-3.4-.3-6.4-3.3-6.8-6.8z" fill="#fff"/>
  </svg>
  <svg class="contact-icon" style="top:1038px" viewBox="0 0 20 20" aria-hidden="true">
    <g fill="none" stroke="#fff" stroke-width="1.3">
      <circle cx="10" cy="10" r="8"/>
      <ellipse cx="10" cy="10" rx="3.5" ry="8"/>
      <line x1="2" y1="10" x2="18" y2="10"/>
      <line x1="3.5" y1="6" x2="16.5" y2="6"/>
      <line x1="3.5" y1="14" x2="16.5" y2="14"/>
    </g>
  </svg>
  <svg class="contact-icon" style="top:1074px" viewBox="0 0 20 20" aria-hidden="true">
    <circle cx="10" cy="10" r="8.5" fill="none" stroke="#fff" stroke-width="1.5"/>
    <path d="M10 4.5a3.3 3.3 0 0 0-3.3 3.3c0 2.5 3.3 6.7 3.3 6.7s3.3-4.2 3.3-6.7A3.3 3.3 0 0 0 10 4.5z" fill="none" stroke="#fff" stroke-width="1.3"/>
    <circle cx="10" cy="7.9" r="1.1" fill="#fff"/>
  </svg>

  <address class="contact-list">
    <div>(555) 210-4417<br>(555) 380-9162(Main)</div>
    <div>jsmith@parcelwisehq.example<br>www.parcelwisehq.example</div>
    <div>82 Harbor Lane<br>Fairview, MI 40000</div>
  </address>
</main>
</body>
</html>
```